Luxury Wine Label for New Startup Winery

We need a wine label for our new winery startup. We have worked with a local designer but do not feel the resulting label / logo have the elevation required to present our brand as a luxury wine. Our winery is called "Quailbrook Vineyards" and we are focused on extremely high quality hand crafted artisan and estate wines from the Pacific Northwest.
We would like to see designs that utilize a tree line, or other imagery that represents the "Quailbrook" part of our company name. Another interesting feature could be wood grain.
A logo will be required based on your design so please design with this in mind:
This logo should be consistent with the wine bottle label design, and should be representative of our high end exclusive wine while giving a sense of place (Oregon/ Pacific Northwest.)
I will supply an image of the design we received from our local designer, PLEASE NOTE: in general we do like wood grain and tree line concepts but feel the execution was poorly done.
ATTN: Logo design should be suitable for use on: Bottles (Red wine/rose/white wine), Bussiness cards, vehicle signage, business signage, etc
P.S.:
If you have a design that is not outside the box we are still interested in seeing it.
Label is for a burgundy style bottle with a label height of 3.5 - 4" and a width of 3.5-4"
any label <= 4"x4" and >=3.5"x3.5" will be acceptable:
HOWEVER Width should be greater than or equal to height due to the bottle format
Target Market(s)
Wine enthusiasts with adequate discretionary budgets to afford $100 bottles of wine.
Industry/Entity Type
Wine / Winery
Requirements
Must have
- A sense of luxury, a feel of exclusivity, and a theme consistent with our product and brand name
Nice to have
- Tree line, wood grain or other wood themes. Serif fonts
Should not have
- anything cheesy, off topic, hard to read script fonts or anything that makes the label hard to read from a few feet away or too busy

```html
<!DOCTYPE html>
<html lang="en">
<head>
<meta charset="utf-8">
<title>Quailbrook Vineyards — Syrah Label</title>
<link href="https://fonts.googleapis.com/css2?family=Cinzel:wght@400;600;700&display=swap" rel="stylesheet">
<style>
  :root {
    --backdrop: #d2d2d2;
    --label-paper: #ffffff;
    --label-shade: #e6e6e6;
    --ink: #1f1f1f;
    --wine: #8a1538;
    --wine-deep: #5e0d26;
    --wine-light: #c2325e;
    --wood-light: #a08d74;
    --wood-mid: #7d6a53;
    --wood-dark: #5a4a39;
  }
  * { box-sizing: border-box; margin: 0; padding: 0; }
  html, body { width: 1200px; height: 750px; overflow: hidden; }
  body {
    background: var(--backdrop);
    font-family: "Cinzel", "Times New Roman", serif;
    position: relative;
  }
  .wine-label {
    position: absolute;
    left: 280px;
    top: 97px;
    width: 640px;
    height: 556px;
    background: radial-gradient(ellipse at 50% 40%, var(--label-paper) 0%, var(--label-paper) 45%, var(--label-shade) 100%);
    box-shadow: 0 6px 18px rgba(0,0,0,0.18);
  }
  .wood-band {
    position: absolute;
    left: 0; top: 0;
    width: 100%;
    height: 32px;
    background: linear-gradient(180deg, var(--wood-light) 0%, var(--wood-mid) 55%, var(--wood-dark) 100%);
  }
  .brand-line {
    position: absolute;
    top: 84px;
    left: 0; width: 100%;
    display: flex;
    justify-content: center;
    align-items: center;
    gap: 14px;
    color: var(--ink);
    font-size: 25px;
    font-weight: 600;
    letter-spacing: 1px;
  }
  .brand-dot {
    width: 30px; height: 30px;
    border-radius: 50%;
    background: var(--ink);
  }
  .splash-art {
    position: absolute;
    left: 170px;
    top: 170px;
    width: 300px;
    height: 260px;
    border-radius: 48% 52% 45% 55% / 50% 44% 56% 50%;
    background: radial-gradient(ellipse at 45% 45%, var(--wine-deep) 0%, var(--wine) 45%, var(--wine-light) 80%, rgba(194,50,94,0) 100%);
  }
  .varietal {
    position: absolute;
    top: 452px;
    left: 0; width: 100%;
    text-align: center;
    color: var(--wine);
    font-size: 30px;
    font-weight: 700;
    letter-spacing: 3px;
  }
  .vintage-rule {
    position: absolute;
    left: 0; top: 506px;
    width: 100%;
    height: 34px;
  }
  .vintage-rule svg { display: block; }
  .vintage-year {
    position: absolute;
    left: 50%;
    top: 506px;
    transform: translateX(-50%);
    width: 104px;
    height: 34px;
    border-radius: 17px;
    background: linear-gradient(180deg, var(--wood-light), var(--wood-mid));
    color: var(--ink);
    font-size: 21px;
    font-weight: 700;
    display: flex;
    align-items: center;
    justify-content: center;
    letter-spacing: 1px;
  }
</style>
</head>
<body>
  <main class="wine-label">
    <div class="wood-band" role="img" aria-label="Weathered wood grain band"></div>

    <div class="brand-line">
      <span class="brand-word">QUAILBROOK</span>
      <span class="brand-dot"></span>
      <span class="brand-word">VINEYARDS</span>
    </div>

    <div class="splash-art" role="img" aria-label="Red wine splash with a grape leaf pressed into it"></div>

    <h1 class="varietal">SYRAH</h1>

    <div class="vintage-rule">
      <svg width="640" height="34" viewBox="0 0 640 34" aria-hidden="true">
        <line x1="0" y1="14" x2="640" y2="14" stroke="#7d6a53" stroke-width="2"/>
        <line x1="0" y1="21" x2="640" y2="21" stroke="#5a4a39" stroke-width="3"/>
      </svg>
    </div>
    <div class="vintage-year">2024</div>
  </main>
</body>
</html>
```